Foot doctor needs feet friendly business cards.

Business cards for Podiatrist. Needs to look professional and modern. Back side put an appointment card, and try to put a little basic street map somewhere on card along with all of our contact info below:

Marcus Dovan, DPM, Inc.
Diplomate, National Council of Lower Limb Medicine
Call: 1.877.Toes.482
1.555.283.9146
Fax: 1.555.671.3820
Email: info@DrDovanclinic.example
Web: www.DrDovanclinic.example
2847 W. Harbor Ln. Suite 204
Costa Mesa, CA 90000

```html
<!DOCTYPE html>
<html lang="en">
<head>
<meta charset="utf-8">
<title>Marcus Dovan, DPM — Business Card</title>
<link rel="stylesheet" href="https://fonts.googleapis.com/css2?family=Source+Sans+3:ital,wght@0,400;0,600;0,700;1,400;1,600&display=swap">
<style>
  :root {
    --stage: #000000;
    --card: #ecf0f3;
    --ink: #111418;
    --brand: #1f4e79;
    --rule: #6d7378;
    --sheet: #f6f7f8;
    --skin: #e2ad8f;
    --skin-deep: #c98d6c;
  }
  * { margin: 0; padding: 0; box-sizing: border-box; }
  html, body {
    width: 1200px; height: 900px; overflow: hidden;
    background: var(--stage);
    font-family: "Source Sans 3", "Myriad Pro", Arial, sans-serif;
    color: var(--ink);
  }
  .stage { position: relative; width: 1200px; height: 900px; }
  .card {
    position: absolute; top: 200px; width: 310px; height: 502px;
    background: var(--card); overflow: hidden;
  }
  .card--front { left: 265px; border-radius: 48px 0 48px 0; }
  .card--back  { left: 641px; width: 309px; border-radius: 0 48px 0 48px; }

  .photo-area {
    position: absolute; left: 0; right: 0; bottom: 0; height: 240px;
    background:
      linear-gradient(180deg, rgba(236,240,243,0) 0%, var(--sheet) 22%, var(--sheet) 34%, rgba(246,247,248,0) 48%),
      linear-gradient(180deg, var(--sheet) 0%, #efd3c2 55%, var(--skin) 78%, var(--skin-deep) 100%);
  }

  /* front */
  .name {
    position: absolute; left: 28px; top: 47px;
    color: var(--brand); font-weight: 600; font-size: 21px; letter-spacing: 0.3px;
    white-space: nowrap;
  }
  .name .credentials { font-size: 17px; }
  .text-block { position: absolute; left: 28px; font-size: 15px; line-height: 21px; }
  .title { top: 75px; }
  .address { top: 134px; }
  .contacts { top: 199px; list-style: none; }
  .contacts li { position: relative; padding-left: 18px; }
  .contacts svg { position: absolute; left: 1px; top: 6px; width: 11px; height: 10px; fill: var(--brand); }

  /* back */
  .appt-heading {
    position: absolute; left: 28px; top: 30px;
    color: var(--brand); font-style: italic; font-weight: 600; font-size: 16px;
  }
  .field {
    position: absolute; left: 26px; font-size: 14px; line-height: 18px;
  }
  .field-line { position: absolute; height: 1px; background: var(--rule); }
  .notice {
    position: absolute; left: 18px; top: 210px;
    font-style: italic; font-weight: 600; font-size: 14.5px; line-height: 23px;
  }
</style>
</head>
<body>
<main class="stage">
  <section class="card card--front" aria-label="Business card front">
    <div class="photo-area" role="img" aria-label="Photo of bare feet peeking out from under white bed sheets"></div>
    <h1 class="name">MARCUS DOVAN<span class="credentials">, DPM, INC.</span></h1>
    <p class="text-block title">Diplomate, National Council<br>of Lower Limb Medicine</p>
    <p class="text-block address">2847 W. Harbor Ln. Suite 204<br>Costa Mesa, CA 90000</p>
    <ul class="text-block contacts">
      <li><svg viewBox="0 0 12 10"><path d="M1 3C1 1 3 0 6 0s5 1 5 3l-2 1-1-2H4L3 4zM2 5h8l1 5H1z"/></svg>1.877.Toes.482</li>
      <li>1.555.283.9146</li>
      <li><svg viewBox="0 0 12 10"><path d="M3 0h6v3H3zM1 3h10v7H1zm2 2v2h2V5z"/></svg>1.555.671.3820</li>
      <li><svg viewBox="0 0 12 10"><path d="M0 1h12v1L6 6 0 2zM0 3.5l6 4 6-4V9H0z"/></svg>info@DrDovanclinic.example</li>
      <li><svg viewBox="0 0 12 10"><path d="M7 1l2-1 3 3-1 2-3 3-2-2 1-1 1 1 2-2-1-1-2 2-1-1zM5 9L3 10 0 7l1-2 3-3 2 2-1 1-1-1-2 2 1 1 2-2 1 1z"/></svg>www.DrDovanclinic.example</li>
    </ul>
  </section>

  <section class="card card--back" aria-label="Appointment card back">
    <div class="photo-area" role="img" aria-label="Photo of bare feet peeking out from under white bed sheets"></div>
    <h2 class="appt-heading">Appointment</h2>
    <span class="field" style="top:74px">For :</span>
    <span class="field-line" style="left:56px;width:213px;top:90px"></span>
    <span class="field" style="top:108px">Date :</span>
    <span class="field-line" style="left:64px;width:82px;top:124px"></span>
    <span class="field" style="top:108px;left:147px">Time :</span>
    <span class="field-line" style="left:187px;width:84px;top:124px"></span>
    <span class="field" style="top:142px">Location :</span>
    <span class="field-line" style="left:88px;width:184px;top:158px"></span>
    <span class="field-line" style="left:25px;width:247px;top:188px"></span>
    <p class="notice">If you&nbsp; are unable to keep appointment,<br>please contact<br>us as soon as possible. Call&nbsp; 555 210 4482</p>
  </section>
</main>
</body>
</html>
```